Venture 482 - Lumora Book Cover

I am looking for a Lumora book cover for my book about "Venture 482".
The Book is Titled:
Venture 482 Ascended
Shaping Outcomes: Paths To Unlocking Cosmic Truths
Author is Dorian Pell
Here is a book description that may help you understand more about it:
Inspired by the genius of Edwin Marlowe, this comprehensive guide delves into the ancient wisdom and cutting-edge science behind the 482 method, a powerful tool for manifesting your desires. Whether you're seeking personal growth, financial success, or spiritual enlightenment, this book provides advanced techniques and methods to transform your dreams into reality.
Any questions please ask.
Thanks
Owen

```html
<!DOCTYPE html>
<html lang="en">
<head>
<meta charset="utf-8">
<title>Venture 482 Ascended – Book Cover</title>
<link rel="stylesheet" href="https://fonts.googleapis.com/css2?family=Poppins:wght@800;900&family=Montserrat:wght@800&family=Tinos:wght@400;700&family=Cinzel:wght@400&display=swap">
<style>
  :root {
    --page-bg: #e4e4e2;
    --cover-red: #8a1a0c;
    --cover-red-deep: #4d0804;
    --cover-red-glow: #b8321a;
    --title-gold: #f6d88a;
    --title-ice: #e3f3fb;
    --text-white: #ffffff;
    --text-cream: #f7efe6;
    --author-blush: #f3cfc5;
    --shadow-ink: #14101a;
  }
  * { margin: 0; padding: 0; box-sizing: border-box; }
  html, body {
    width: 1200px; height: 1131px; overflow: hidden;
    background: var(--page-bg);
  }
  .cover {
    position: absolute; left: 226px; top: 0;
    width: 748px; height: 1131px; overflow: hidden;
    background:
      radial-gradient(ellipse 70% 40% at 30% 12%, rgba(220,70,40,0.45), transparent 70%),
      radial-gradient(ellipse 60% 45% at 55% 45%, rgba(170,40,20,0.35), transparent 75%),
      linear-gradient(180deg, var(--cover-red) 0%, #761309 50%, var(--cover-red-deep) 100%);
  }
  .emblem {
    position: absolute; left: 139px; top: 265px;
    width: 490px; height: 490px;
  }
  .title-kicker {
    position: absolute; left: 145px; top: 340px;
    font-family: "Poppins", sans-serif; font-weight: 900;
    font-size: 50px; line-height: 1; letter-spacing: -2px;
    color: var(--title-gold);
    text-shadow: 4px 4px 0 var(--shadow-ink);
  }
  .title-number {
    position: absolute; left: 150px; top: 388px;
    font-family: "Montserrat", sans-serif; font-weight: 800;
    font-size: 262px; line-height: 1; letter-spacing: -14px;
    color: var(--title-ice);
    text-shadow: -4px 4px 6px rgba(20,16,26,0.35);
  }
  .title-edition {
    position: absolute; left: 130px; width: 500px; top: 622px;
    text-align: center;
    font-family: "Montserrat", sans-serif; font-weight: 800;
    font-size: 46px; line-height: 1; letter-spacing: 18px;
    color: var(--text-white);
    text-shadow: 4px 4px 0 var(--shadow-ink);
  }
  .subtitle {
    position: absolute; left: 0; width: 100%; top: 795px;
    text-align: center;
    font-family: "Tinos", serif; color: var(--text-cream);
    font-size: 27px; line-height: 37px;
  }
  .subtitle strong { font-weight: 700; letter-spacing: -0.5px; display: block; }
  .author {
    position: absolute; left: 0; width: 100%; top: 1022px;
    text-align: center;
    font-family: "Cinzel", serif; font-weight: 400;
    font-size: 58px; line-height: 1; letter-spacing: 12px;
    color: var(--author-blush);
    text-shadow: 6px 10px 0 rgba(40,6,4,0.55);
  }
</style>
</head>
<body>
  <main class="cover">
    <svg class="emblem" viewBox="0 0 490 490" role="img" aria-label="Sacred geometry emblem illustration behind the title">
      <defs>
        <radialGradient id="emblemGlow" cx="50%" cy="50%" r="50%">
          <stop offset="0%" stop-color="#d9c9c4" stop-opacity="0.35"/>
          <stop offset="60%" stop-color="#c9a9a0" stop-opacity="0.22"/>
          <stop offset="100%" stop-color="#c9a9a0" stop-opacity="0"/>
        </radialGradient>
      </defs>
      <circle cx="245" cy="245" r="240" fill="url(#emblemGlow)"/>
    </svg>

    <h1>
      <span class="title-kicker">VENTURE</span>
      <span class="title-number">482</span>
      <span class="title-edition">ASCENDED</span>
    </h1>

    <p class="subtitle">
      <strong>SHAPING OUTCOMES:</strong>
      Paths to unlocking<br>cosmic truths
    </p>

    <p class="author">DORIAN PELL</p>
  </main>
</body>
</html>
```